Business card for Eyelash extension salon in Beverly Hills,California USA

We need new business card for our salon in Beverly Hills. The salon name is 'Lashvera' . We would like to have...Business name: Lashvera Name of person: will provide later Address 4720 N.Alder Crest Ave Beverly Hills , CA 90210 Phone: will provide later (Text only) Web: www.lashverastudio.example Snapgrid icon, Circlebook icon follow us for seasonal campaign and news @lashverastudiolounge Design should look elegant, high-end, clean, simple, cohesive with my brand. Please refer my brand board. Business name color will be metallic bronzy color. Im thinking grey background or white background. Thanks

Target Market(s)

25-35. Gender neutral. People who are in Entertainment business industry.
This is High-end Eyelash extension salon in Beverly Hills

Industry/Entity Type

Beauty Salon

Contact Information for Business Card

Business name: Lashvera
Name of person: will provide later
Address 4720 N.Alder Crest Ave Beverly Hills , CA 90210
Phone: will provide later (Text only)
Web: www.lashverastudio.example
Snapgrid icon, Circlebook icon
follow us for seasonal campaign and news @lashverastudiolounge

Requirements
Must have
• Beautiful, elegant, clean and simple look but very attractive and modern
Should not have
• We don't like too clutter, too busy designs.

```html
<!DOCTYPE html>
<html lang="en">
<head>
<meta charset="utf-8">
<title>Lashvera Business Card</title>
<link rel="stylesheet" href="https://fonts.googleapis.com/css2?family=Work+Sans:wght@400;500&display=swap">
<style>
  :root {
    --page-bg: #e9e4df;
    --card-bronze-light: #8c6852;
    --card-bronze-dark: #6f4f3c;
    --panel-dark: #2f3032;
    --panel-mid: #4a4b4d;
    --logo-bronze: #c99f80;
    --tagline-grey: #8e8e8e;
    --text-cream: #f3e9e0;
    --text-soft: #e4d5c9;
  }
  html, body {
    margin: 0;
    padding: 0;
    width: 1200px;
    height: 1047px;
    overflow: hidden;
    background: var(--page-bg);
    font-family: "Work Sans", sans-serif;
  }
  .business-card {
    position: absolute;
    left: 100px;
    top: 252px;
    width: 1000px;
    height: 543px;
    border-radius: 24px;
    overflow: hidden;
    background: linear-gradient(160deg, var(--card-bronze-light), var(--card-bronze-dark));
    box-shadow: 0 18px 40px rgba(60, 40, 30, 0.25);
  }
  .brand-panel {
    position: absolute;
    left: 0;
    top: 0;
    width: 337px;
    height: 100%;
    background: linear-gradient(90deg, var(--panel-dark) 0%, var(--panel-mid) 45%, var(--panel-dark) 100%);
  }
  .brand-name {
    position: absolute;
    left: 160px;
    top: 280px;
    transform: translate(-50%, -50%) rotate(-90deg);
    margin: 0;
    font-size: 72px;
    font-weight: 400;
    letter-spacing: 2px;
    color: var(--logo-bronze);
    white-space: nowrap;
  }
  .brand-tagline {
    position: absolute;
    left: 258px;
    top: 190px;
    transform: translate(-50%, -50%) rotate(-90deg);
    margin: 0;
    font-size: 12px;
    letter-spacing: 3px;
    color: var(--tagline-grey);
    white-space: nowrap;
  }
  .contact-block {
    position: absolute;
    left: 417px;
    top: 0;
    right: 40px;
    color: var(--text-cream);
  }
  .contact-block > * {
    position: absolute;
    left: 0;
    margin: 0;
    white-space: nowrap;
  }
  .person-name {
    top: 62px;
    font-size: 40px;
    font-weight: 500;
    letter-spacing: 1.5px;
  }
  .person-title {
    top: 112px;
    font-size: 23px;
    font-weight: 400;
    letter-spacing: 1px;
    color: var(--text-soft);
  }
  .contact-lines {
    top: 180px;
    font-size: 21px;
    line-height: 29px;
    letter-spacing: 0.6px;
  }
  .contact-lines .label { font-weight: 500; }
  .studio-name {
    top: 296px;
    font-size: 21px;
    font-weight: 500;
    letter-spacing: 1.2px;
  }
  .studio-address {
    top: 330px;
    font-style: normal;
    font-size: 21px;
    line-height: 29px;
    letter-spacing: 1.4px;
    color: var(--text-soft);
  }
  .social-row {
    top: 420px;
    display: flex;
    gap: 28px;
    font-size: 19px;
    letter-spacing: 0.8px;
    color: var(--text-soft);
  }
  .social-item {
    display: flex;
    align-items: center;
    gap: 9px;
  }
  .social-dot {
    width: 12px;
    height: 12px;
    border-radius: 50%;
    background: var(--logo-bronze);
  }
  .social-handle {
    top: 456px;
    font-size: 19px;
    letter-spacing: 0.8px;
    color: var(--text-soft);
  }
</style>
</head>
<body>
  <div class="business-card">
    <div class="brand-panel">
      <p class="brand-name">Lashvera</p>
      <p class="brand-tagline">BEVERLY HILLS</p>
    </div>
    <div class="contact-block">
      <h1 class="person-name">Noel Carrow</h1>
      <p class="person-title">Director</p>
      <p class="contact-lines">
        <span class="label">Mobile:</span> 0412 555 019<br>
        <span class="label">Email:</span> noel@lashverastudio.example<br>
        <span class="label">Web:</span> www.lashverastudio.example
      </p>
      <p class="studio-name">LASHVERA</p>
      <address class="studio-address">
        4720 N.Alder Crest Ave<br>
        Beverly Hills , CA 90210
      </address>
      <div class="social-row">
        <span class="social-item"><span class="social-dot"></span>Snapgrid</span>
        <span class="social-item"><span class="social-dot"></span>Circlebook</span>
      </div>
      <p class="social-handle">Follow us @lashverastudiolounge</p>
    </div>
  </div>
</body>
</html>
```